Redesign Of Current Landing Page

I need to redesign this landing page https://www.brightlanepromo.biz/?page=landing&landing=23 (Please do not opt in because when you do it will show you the home page. Please clear your cookies before going to this url above to view the 1 page landing page.)

Please use my updated website as a reference for colors and logo.
http://sitecradlewerk.com/dh/bpq/index.html

I would like the call to action to be a button that opens into a lead form...

Button would be "Download Samples"

Target Market(s)

small business owners

Industry/Entity Type

Marketing

Number of Pages Required

1 page

Colors

Designer to choose colors to be used in the design.

Requirements
Must have
• must be full responsive on all devices
Nice to have
• must have a legitimate professional apeal to it
Should not have
• open

```html
<!DOCTYPE html>
<html lang="en">
<head>
<meta charset="utf-8">
<title>Bright Lane Promotions Group – Landing</title>
<link href="https://fonts.googleapis.com/css2?family=Bree+Serif&family=Poppins:wght@400;500&display=swap" rel="stylesheet">
<style>
:root{
  --blue:#0d6cc0;
  --orange:#ffa800;
  --orange-soft:#f7c07a;
  --ink:#333;
  --muted:#666;
  --line:#9a9a9a;
  --card:#f4f4f4;
  --footer:#1f1f1f;
  --white:#fff;
}
*{margin:0;padding:0;box-sizing:border-box}
html,body{width:754px;height:1200px;overflow:hidden;background:var(--white)}
body{position:relative;font-family:'Poppins',sans-serif;color:var(--muted)}
.abs{position:absolute}
.serif{font-family:'Bree Serif',serif}

.site-header{left:0;top:0;width:754px;height:35px;background:var(--white)}
.brand{left:62px;top:7px;display:flex;align-items:center;gap:6px;font-family:'Bree Serif',serif;font-size:17px;color:var(--ink)}
.brand-dot{width:18px;height:18px;border-radius:50%;background:var(--blue)}
.main-nav{right:62px;top:13px;display:flex;gap:27px;font-size:7.5px;color:var(--ink)}

.hero{left:0;top:35px;width:754px;height:286px;background:linear-gradient(135deg,#3b3c3e,#1d1e20 55%,#4a4b4d)}
.hero-copy{left:0;top:72px;width:754px;text-align:center;color:var(--white);font-family:'Bree Serif',serif}
.hero-title{font-size:29px;letter-spacing:1px;line-height:1}
.hero-sub{font-size:16px;line-height:25.5px;margin-top:9px}
.hero-cta{left:230px;top:230px;width:302px;height:28px;background:var(--blue);color:var(--white);font-family:'Bree Serif',serif;font-size:15px;text-align:center;line-height:28px}

.section-rule{left:62px;width:630px;height:1px;background:var(--line)}
.section-label{height:22px;border:1px solid var(--line);background:var(--white);color:var(--blue);font-family:'Bree Serif',serif;font-size:12.5px;text-align:center;line-height:20px}
.body-copy{left:84px;width:586px;font-size:6.4px;line-height:12.8px;text-align:center;color:var(--muted)}
.btn{height:23px;background:var(--orange);color:var(--white);font-family:'Bree Serif',serif;font-size:10px;text-align:center;line-height:23px;box-shadow:0 2px 0 #e39200}
.btn.caps{font-family:'Poppins',sans-serif;font-weight:500;font-size:7.4px}

.why-title{left:0;top:624px;width:754px;text-align:center;color:var(--blue);font-family:'Bree Serif',serif;font-size:16.5px}
.benefit{top:690px;width:150px;height:110px;background:var(--card);text-align:center;font-size:8.6px;line-height:14px;color:var(--muted);padding:0 12px}
.benefit svg{display:block;margin:22px auto 20px}
.benefit.active{background:var(--orange);color:var(--white)}
.benefit.active svg{margin-bottom:22px}

.quote-card{top:877px;width:173px;height:199px;background:#f8f8f8;text-align:center;padding:0 21px}
.quote-card svg{display:block;margin:24px auto 16px}
.quote-text{font-size:6.4px;line-height:12.8px;text-align:justify;text-align-last:center}
.avatar{top:1050px;width:55px;height:55px;border-radius:50%;border:2px solid var(--orange);background:radial-gradient(circle at 50% 45%,#d9b79a,#8c6b55)}
.reviewer{top:1112px;width:173px;text-align:center;font-family:'Bree Serif',serif;font-size:10.5px;line-height:16.5px;color:var(--ink)}

.site-footer{left:0;top:1166px;width:754px;height:34px;background:var(--footer);color:var(--white);font-size:6.6px}
.contact-line{left:62px;top:12px;display:flex;align-items:center;gap:5px}
.copyright{right:72px;top:13px}
</style>
</head>
<body>

<header class="abs site-header">
  <div class="abs brand"><span class="brand-dot"></span>BLPG</div>
  <nav class="abs main-nav"><span>Home</span><span>About Us</span><span>Testimonials</span><span>Samples</span><span>FAQ</span><span>Contact</span></nav>
</header>

<section class="abs hero" role="img" aria-label="Overhead photo of business people meeting around a table with laptops and papers"></section>
<div class="abs hero-copy">
  <h1 class="hero-title">ATTRACT MORE CUSTOMERS</h1>
  <p class="hero-sub">Who Spend More Money With Your Business More Often!<br>Using Free Vacation &amp; Cruise Certificates And Other<br>Incentives Without Breaking The Bank!</p>
</div>
<div class="abs hero-cta">Download Free Samples Of Our Incentives</div>

<!-- Imagine -->
<div class="abs section-rule" style="top:352px"></div>
<div class="abs section-label" style="left:328px;top:341px;width:99px">Imagine</div>
<p class="abs body-copy" style="top:379px">Being able to create exciting give away promotions that will boost your sales without ever having to worry about cost. Bright Lane Promotions Group, Inc. provides high-perceived value promotional incentives to businesses that want to advertise an exciting Give Away that will instantly attract more customers from your existing advertising efforts. Your business can give away incentive certificates that are redeemable for luxury hotel &amp; resort stays with airfare.</p>
<div class="abs btn" style="left:255px;top:432px;width:86px">Read More</div>
<div class="abs btn" style="left:354px;top:431px;width:156px">Download Free Samples</div>

<!-- How -->
<div class="abs section-rule" style="top:494px"></div>
<div class="abs section-label" style="left:308px;top:482px;width:138px;height:24px;line-height:22px">How Can We Do It?</div>
<p class="abs body-copy" style="top:524px">We help fill empty rooms for thousands of hotels and resorts in hundreds of destinations around the world as well as the major cruise lines. Hotels and resorts are rarely full so when we place someone in their empty rooms, they end up making it up when travelers spend money on room service, spa services, eat at their in-house restaurants, casino and take advantage of other amenities that drive revenue.</p>
<div class="abs btn" style="left:258px;top:581px;width:85px">Read More</div>
<div class="abs btn caps" style="left:357px;top:581px;width:149px">REQUEST FREE SAMPLE PACKAGE</div>

<!-- Why -->
<h2 class="abs why-title">Why Offer Incentives To Customers?</h2>
<p class="abs body-copy" style="left:120px;width:514px;top:653px">Bright Lane Promotions Group, Inc. provides high-perceived value promotional incentives to businesses that want to advertise an exciting Give Away that will instantly attract more customers from your existing advertising efforts.</p>

<div class="abs benefit" style="left:62px">
  <svg width="34" height="26" viewBox="0 0 34 26" fill="#0d6cc0"><rect x="0" y="0" width="2" height="26"/><rect x="0" y="24" width="34" height="2"/><rect x="6" y="12" width="4" height="10"/><rect x="12" y="8" width="4" height="14"/><rect x="18" y="14" width="4" height="8"/><rect x="24" y="4" width="4" height="18"/></svg>
  Increase Responses From Your Existing Ads
</div>
<div class="abs benefit" style="left:222px">
  <svg width="32" height="28" viewBox="0 0 32 28" fill="#0d6cc0"><circle cx="11" cy="16" r="8"/><circle cx="11" cy="16" r="3" fill="#f4f4f4"/><circle cx="25" cy="7" r="5.5"/><circle cx="25" cy="7" r="2" fill="#f4f4f4"/><circle cx="25" cy="22" r="4.5"/><circle cx="25" cy="22" r="1.6" fill="#f4f4f4"/></svg>
  Insure The Sale Over Your Competition
</div>
<div class="abs benefit active" style="left:382px">
  <svg width="30" height="28" viewBox="0 0 30 28" fill="none" stroke="#fff" stroke-width="2.4" stroke-linejoin="round"><path d="M28 2 2 13l9 3 3 10 4-7 7 5z"/><path d="M28 2 11 16"/></svg>
  Build Brand Awareness and Trust
</div>
<div class="abs benefit" style="left:542px">
  <svg width="30" height="28" viewBox="0 0 30 28" fill="#0d6cc0"><rect x="4" y="3" width="12" height="14" rx="2" transform="rotate(-45 10 10)"/><rect x="15" y="14" width="4" height="16" transform="rotate(-45 17 22)"/></svg>
  Boost Repeat and Referral Business
</div>

<!-- Testimonials -->
<div class="abs section-rule" style="top:838px"></div>
<div class="abs section-label" style="left:308px;top:827px;width:138px;height:23px;line-height:21px">Testimonials</div>

<div class="abs quote-card" style="left:92px">
  <svg width="22" height="18" viewBox="0 0 22 18" fill="#f7c07a"><path d="M0 8Q0 1 8 0v3Q4 4 4 8h5v10H0zM13 8q0-7 8-8v3q-4 1-4 5h5v10h-9z"/></svg>
  <p class="quote-text">I began using your incentives two years ago to boost lead generation efforts. I have experienced a 63% increase in lead captures. And, even more importantly, my sales have increased as well. The ability to offer unlimited certificates and not having.</p>
</div>
<div class="abs quote-card" style="left:289px">
  <svg width="22" height="18" viewBox="0 0 22 18" fill="#f7c07a"><path d="M0 8Q0 1 8 0v3Q4 4 4 8h5v10H0zM13 8q0-7 8-8v3q-4 1-4 5h5v10h-9z"/></svg>
  <p class="quote-text">Lorem Ipsum is simply dummy text of the printing and typesetting industry. Lorem Ipsum has been the industry's standard dummy text ever since the 1500s, when an unknown printer took a galley of type and scrambled it to make a type specimen book.</p>
</div>
<div class="abs quote-card" style="left:489px">
  <svg width="22" height="18" viewBox="0 0 22 18" fill="#f7c07a"><path d="M0 8Q0 1 8 0v3Q4 4 4 8h5v10H0zM13 8q0-7 8-8v3q-4 1-4 5h5v10h-9z"/></svg>
  <p class="quote-text">Lorem Ipsum is simply dummy text of the printing and typesetting industry. Lorem Ipsum has been the industry's standard dummy text ever since the 1500s, when an unknown printer took a galley of type and scrambled it to make a type specimen book.</p>
</div>

<div class="abs avatar" style="left:146px" role="img" aria-label="Portrait photo of reviewer Dan R."></div>
<div class="abs avatar" style="left:345px" role="img" aria-label="Portrait photo of reviewer Lena Marsh"></div>
<div class="abs avatar" style="left:547px" role="img" aria-label="Portrait photo of reviewer Carla"></div>

<div class="abs reviewer" style="left:88px">Dan R.<br>Millersville, TN</div>
<div class="abs reviewer" style="left:286px">Lena Marsh<br>Millersville, TN</div>
<div class="abs reviewer" style="left:487px">Carla<br>Millersville, TN</div>

<footer class="abs site-footer">
  <div class="abs contact-line">
    <svg width="8" height="8" viewBox="0 0 8 8"><rect width="8" height="8" rx="1.5" fill="#fff"/><path d="M2 2.2q.5 2.8 3.8 3.8l.6-.9-1-.6-.5.4Q3.7 4.4 3.2 3.2l.4-.5L3 1.6z" fill="#1f1f1f"/></svg>
    <span>1-800-555-0142</span>
    <svg width="8" height="8" viewBox="0 0 8 8" style="margin-left:5px"><circle cx="4" cy="4" r="3.4" fill="none" stroke="#fff" stroke-width="1"/><path d="M4 2v2l1.3 1" stroke="#fff" stroke-width=".9" fill="none"/></svg>
    <span>Mon-Fri 8am-5pm PST</span>
  </div>
  <div class="abs copyright">Copyright 2017 Bright Lane Promotions Group, Inc. All rights reserved.</div>
</footer>

</body>
</html>
```